Business Cards for a law firm

Business cards for our law firm. Use our silhoette logo and OAK PARTNERS - check our website (www.oakpartners.example)

Contact Information for Business Card

our silhouette logo, OAK PARTNERS, 800-555-0147, Dorian Pemberton, dorian@oakpartners.example

Requirements
Must have
• our silhouette logo, OAK PARTNERS, 800-555-0147, Dorian Pemberton, dorian@oakpartners.example

```html
<!DOCTYPE html>
<html lang="en">
<head>
<meta charset="utf-8">
<title>Oak Partners Business Cards</title>
<link rel="stylesheet" href="https://fonts.googleapis.com/css2?family=Cinzel:wght@600;700&family=Open+Sans:wght@400&display=swap">
<style>
  :root {
    --navy: #1a2f6a;
    --navy-soft: #26407f;
    --white: #ffffff;
    --gold: #f5a623;
    --backdrop: #e9eaed;
  }
  * { margin: 0; padding: 0; box-sizing: border-box; }
  html, body {
    width: 1200px; height: 874px; overflow: hidden;
    background: var(--backdrop);
  }
  .sheet {
    position: relative; width: 1200px; height: 874px;
  }
  .card {
    position: absolute; left: 290px; width: 620px; height: 354px;
    border-radius: 22px; overflow: hidden;
    box-shadow: 0 10px 28px rgba(0,0,0,0.18);
  }
  .card--front { top: 48px; background: var(--white); }
  .card--back { top: 452px; background: var(--navy); }

  .brand {
    font-family: "Cinzel", serif; font-weight: 700;
    letter-spacing: 0.08em; white-space: nowrap;
  }
  .front-brand {
    position: absolute; left: 110px; top: 148px;
    display: flex; align-items: center; gap: 18px;
  }
  .front-brand .mark {
    width: 40px; height: 40px; background: var(--navy);
  }
  .front-brand .brand { color: var(--navy); font-size: 36px; }

  .back-brand {
    position: absolute; left: 40px; top: 40px;
    color: var(--white); font-size: 26px;
  }
  .figure-art {
    position: absolute; right: 0; top: 0; width: 270px; height: 354px;
    background: linear-gradient(180deg, rgba(255,255,255,0.08), rgba(255,255,255,0.9));
  }
  .holder {
    position: absolute; left: 40px; top: 208px;
  }
  .holder-name {
    font-family: "Cinzel", serif; font-weight: 700;
    color: var(--gold); font-size: 22px; letter-spacing: 0.04em;
  }
  .holder-rule {
    width: 26px; height: 2px; background: var(--gold); margin: 10px 0 14px;
  }
  .contact-list { list-style: none; }
  .contact-item {
    display: flex; align-items: center; gap: 10px;
    font-family: "Open Sans", sans-serif; font-size: 15px;
    color: var(--white); line-height: 22px;
  }
  .contact-item svg { width: 13px; height: 13px; flex: none; }
</style>
</head>
<body>
<main class="sheet">
  <section class="card card--front" aria-label="Card front">
    <div class="front-brand">
      <span class="mark"></span>
      <span class="brand">OAK PARTNERS</span>
    </div>
  </section>

  <section class="card card--back" aria-label="Card back">
    <div class="brand back-brand">OAK PARTNERS</div>
    <div class="figure-art" role="img" aria-label="Large white silhouette artwork of two standing figures"></div>
    <div class="holder">
      <div class="holder-name">Dorian Pemberton</div>
      <div class="holder-rule"></div>
      <ul class="contact-list">
        <li class="contact-item">
          <svg viewBox="0 0 16 16" aria-hidden="true"><path fill="#f5a623" d="M3.5 1l2.5 3-1.5 1.8c.8 2 2.3 3.5 4.2 4.3L10.5 8.5 14 11l-1.2 3C7 14 2 9 2 2.5z"/></svg>
          800-555-0147
        </li>
        <li class="contact-item">
          <svg viewBox="0 0 16 16" aria-hidden="true"><rect x="1" y="3" width="14" height="10" fill="#f5a623"/><path d="M1 3l7 6 7-6" fill="none" stroke="#1a2f6a" stroke-width="1.4"/></svg>
          dorian@oakpartners.example
        </li>
        <li class="contact-item">
          <svg viewBox="0 0 16 16" aria-hidden="true"><circle cx="8" cy="8" r="7" fill="#f5a623"/><path d="M1 8h14M8 1c3 3 3 11 0 14M8 1c-3 3-3 11 0 14" fill="none" stroke="#1a2f6a" stroke-width="1.1"/></svg>
          www.oakpartners.example
        </li>
      </ul>
    </div>
  </section>
</main>
</body>
</html>
```